Etiketten-Design für nachhaltige Rasur- & Pflegeprodukte
> Wir suchen Verpackung und Etiketten für eine Marke für nachhaltige Rasur- & Pflegeprodukte.
Habedere liebe Designer,
„Habedere“ sagt man bei uns in Bayern, es bedeutet Hallo oder auf Wiedersehen, je nach Gelegenheit. In diesem Fall: Hallo.
Vielleicht kennst du uns schon, wir sind greenpines, wir betreiben einen kleinen Shop für Bartpflege & Rasur unter greenpines-shop.de und wir versuchen uns nun an einem neuen Thema: nachhaltige Rasur- & Pflegeprodukte für Frauen.
Das machen wir unter dem Namen „Sanft“.
Weil die Frage schon oft aufkam: Jawohl, wir haben uns dafür die Beine und die Achseln mit einem Rasierhobel rasiert.
> Zielgruppe.
Wir arbeiten an einer neuen Pflegelinie für Frauen, die sich vorwiegend mit der Rasur und den dazugehörigen Pflegeprodukten beschäftigt. Die Zielgruppe sind vor allem online-affine Frauen aus Deutschland, Österreich und der Schweiz, aber sicher auch europaweit im Alter von 21-45.
> Aufgabenstellung.
Wir sind auf der Suche nach einem Konzept für unsere Produktverpackungen bzw. Etiketten. Bei den Pflegeprodukten verzichten wir bewusst auf eine Umverpackung.
Konkret geplant sind ein Rasierhobel, dafür haben wir eine schöne Umverpackung. Außerdem starten wir mit Rasieröl, Rasierseife und einem After Shave Balsam. Es werden später noch andere Artikel dazukommen, eine Deocreme zum Beispiel.
Rasieröl, Rasiercreme und After Shave Balsam duften nach Orangen, es werden zwei oder drei weitere Duftrichtungen folgen, die eine wird beispielsweise nach Beeren duften, die andere nach Pfirsich und Mango – bitte beachte das bei der Erstellung des Konzeptes, die Unterschiede sollten später auf den ersten Blick erkennbar sein.
Zurück zum Thema Orange: Wir würden den Duft als leicht herben Zitrusduft bezeichnen.
> Die Maße.
• Umverpackung Rasierhobel, weißer Karton (165x90x40mm)
• Rasieröl 30ml (Etikett: 100x46mm)
• Rasiercreme 60ml (Etikett: 156x32mm)
• After Shave Balsam 60ml (Etikett: 156x32mm)
> Zwingend erforderliche Angaben.
Da es sich um Kosmetikprodukte handelt, sind einige Angaben auf dem Label zwingend erforderlich, beispielhaft sollen die folgenden Infos als Platzhalter dienen.
• Hergestellt für Friedrich Lautner e.K. von greenpines, Lindenhofweg 7, 83109 Kolbermoor
• Ingredients: Aqua, Stearic Acid, Cocos Nucifera oil, Glycerin, Potassium Hydroxide, Litsea Cubeba oil, (and) Citrus Sinensis Peel oil, Orbignya Oleifera oil, Sodium Hydroxide, Macadamia ternifolia oil, Talc, Kaolin, Citric Acid, Simmondsia chinensis oil, Maris sal, C.I. 77892 (and) Rad Clay, Citral, Limonene, Linalool, Geraniol
• Platz für einen Barcode
• Rasieröl sind 30ml / 1.01 FL.OZ. ODER Creme & Balsam jeweils 60ml / 2.03 FL. OZ.
Wir haben ein Bild der aktuellen Gefäße beigefügt, es kann aber durchaus sein, dass wir uns noch umen..

```html
<!DOCTYPE html>
<html lang="de">
<head>
<meta charset="utf-8">
<title>Sanft Rasiercreme Etikett</title>
<link rel="stylesheet" href="https://fonts.googleapis.com/css2?family=Playfair+Display:wght@900&family=Courier+Prime&display=swap">
<style>
  :root {
    --backdrop: #a3cbc2;
    --label-white: #ffffff;
    --brand-teal: #6f9c92;
    --ink-black: #111111;
    --scent-orange: #d35a32;
    --fruit-orange-soft: #f4c4ad;
    --fruit-orange-faint: #fbe6dc;
    --note-teal: #6f9c92;
    --small-ink: #333333;
  }
  * { margin: 0; padding: 0; box-sizing: border-box; }
  html, body {
    width: 1200px;
    height: 900px;
    overflow: hidden;
    background: var(--backdrop);
  }
  .canvas {
    position: relative;
    width: 1200px;
    height: 900px;
    display: flex;
    align-items: center;
    justify-content: center;
  }
  .product-label {
    position: relative;
    width: 660px;
    height: 484px;
    background: var(--label-white);
    overflow: hidden;
    box-shadow: 0 10px 30px rgba(40, 80, 70, 0.18);
  }
  .fruit-artwork {
    position: absolute;
    left: 330px;
    top: 250px;
    width: 330px;
    height: 234px;
  }
  .brand-mark {
    position: absolute;
    left: 50%;
    top: 33px;
    width: 194px;
    height: 194px;
    transform: translateX(-50%);
    border-radius: 50%;
    background: var(--brand-teal);
    display: flex;
    align-items: center;
    justify-content: center;
  }
  .brand-name {
    font-family: "Courier Prime", monospace;
    font-size: 44px;
    color: var(--label-white);
    letter-spacing: 1px;
  }
  .product-name,
  .scent-name,
  .origin-note,
  .volume {
    position: absolute;
    left: 0;
    width: 100%;
    text-align: center;
  }
  .product-name {
    top: 238px;
    font-family: "Playfair Display", serif;
    font-weight: 900;
    font-size: 56px;
    line-height: 1;
    color: var(--ink-black);
  }
  .scent-name {
    top: 300px;
    font-family: "Courier Prime", monospace;
    font-size: 38px;
    line-height: 1;
    color: var(--scent-orange);
  }
  .origin-note {
    top: 398px;
    font-family: "Courier Prime", monospace;
    font-size: 22px;
    color: var(--note-teal);
  }
  .volume {
    top: 438px;
    font-family: "Courier Prime", monospace;
    font-size: 19px;
    color: var(--small-ink);
  }
</style>
</head>
<body>
<main class="canvas">
  <section class="product-label">
    <svg class="fruit-artwork" viewBox="0 0 330 234" role="img" aria-label="Zarte Linienillustration von Orangen mit Blättern">
      <defs>
        <radialGradient id="fruit-glow" cx="60%" cy="60%" r="60%">
          <stop offset="0%" stop-color="var(--fruit-orange-soft)" stop-opacity="0.55"/>
          <stop offset="100%" stop-color="var(--fruit-orange-faint)" stop-opacity="0"/>
        </radialGradient>
      </defs>
      <rect width="330" height="234" fill="url(#fruit-glow)"/>
    </svg>
    <div class="brand-mark"><span class="brand-name">Sanft</span></div>
    <h1 class="product-name">Rasiercreme</h1>
    <p class="scent-name">Orange Blossom</p>
    <p class="origin-note">handmade in germany</p>
    <p class="volume">30ml / 1.01 FL.OZ</p>
  </section>
</main>
</body>
</html>
```